Torvane Halbridge

Looking for modern business cards.
Clean contemporary design.
Similar to this.
https://www.plumvexa-search.example/imgres?imgurl=https%3A%2F%2Fimg.quorlint-cdn.example%2Fsleek_dark_metal_card_design_540.jpg&imgrefurl=https%3A%2F%2Fwww.quorlint-prints.example%2Fsleek_dark_metal_card_design-918273645501928374&q=modern%20business%20cards

But I'd like the blue to look metallic.

Business

```html
<!DOCTYPE html>
<html lang="en">
<head>
<meta charset="utf-8">
<title>Torvane Halbridge – Business Card</title>
<link rel="stylesheet" href="https://fonts.googleapis.com/css2?family=Roboto:wght@400;500;700&display=swap">
<style>
  :root {
    --backdrop: #e8e5e1;
    --card-white: #f3f3f3;
    --deep-teal: #245870;
    --steel-blue: #2a9cbf;
    --steel-light: #6cc4e0;
    --steel-dark: #1d7fa0;
    --accent-red: #e8402a;
    --ink-light: #ffffff;
  }
  * { margin: 0; padding: 0; box-sizing: border-box; }
  html, body { width: 1200px; height: 960px; overflow: hidden; }
  body {
    position: relative;
    background: var(--backdrop);
    font-family: "Roboto", Arial, sans-serif;
  }
  .card {
    position: absolute;
    width: 600px;
    height: 343px;
    overflow: hidden;
    box-shadow: 0 2px 6px rgba(0,0,0,0.18);
  }
  .card-front { left: 314px; top: 113px; background: var(--deep-teal); }
  .card-back {
    left: 311px; top: 472px;
    background: linear-gradient(135deg, var(--steel-dark) 0%, var(--steel-blue) 35%, var(--steel-light) 55%, var(--steel-blue) 75%, var(--steel-dark) 100%);
  }
  .front-shapes { position: absolute; inset: 0; }
  .brand-lockup {
    position: absolute;
    left: 40px; top: 171px;
    display: flex; align-items: center; gap: 10px;
  }
  .brand-name {
    font-size: 24px; font-weight: 500;
    color: var(--deep-teal);
    letter-spacing: 0.2px;
  }
  .brand-dot {
    width: 10px; height: 10px; border-radius: 50%;
    background: var(--accent-red);
  }
  .contact-block {
    position: absolute;
    right: 31px; top: 64px;
    text-align: right;
    color: var(--ink-light);
  }
  .person-name {
    font-size: 19px; font-weight: 700;
    color: var(--steel-blue);
    letter-spacing: 0.3px;
    line-height: 24px;
  }
  .person-role { font-size: 15px; font-weight: 500; line-height: 20px; }
  .address { margin-top: 20px; font-size: 14.5px; line-height: 19px; padding-right: 1px; }
  .contact-list { list-style: none; margin-top: 10px; font-size: 14.5px; }
  .contact-list li {
    display: flex; justify-content: flex-end; align-items: center;
    gap: 9px; height: 19.3px;
  }
  .contact-icon { width: 13px; height: 13px; fill: var(--steel-blue); flex: none; }
  .back-brand {
    position: absolute; left: 0; right: 0; top: 130px;
    display: flex; justify-content: center; align-items: center; gap: 14px;
  }
  .back-brand-name { font-size: 40px; font-weight: 500; color: var(--ink-light); }
  .back-brand-dot { width: 18px; height: 18px; border-radius: 50%; background: var(--ink-light); }
  .back-url {
    position: absolute; left: 0; right: 0; top: 298px;
    text-align: center;
    font-size: 14px; letter-spacing: 3.2px;
    color: var(--ink-light);
  }
</style>
</head>
<body>
  <section class="card card-front">
    <svg class="front-shapes" width="600" height="343" viewBox="0 0 600 343">
      <defs>
        <linearGradient id="steel-swoosh" x1="0" y1="1" x2="1" y2="0">
          <stop offset="0" stop-color="#1d7fa0"/>
          <stop offset="0.45" stop-color="#2a9cbf"/>
          <stop offset="0.7" stop-color="#7dcbe4"/>
          <stop offset="1" stop-color="#2a9cbf"/>
        </linearGradient>
      </defs>
      <path d="M0 0 H286 C338 38 362 90 358 140 C350 232 252 312 126 343 H0 Z" fill="#f3f3f3"/>
      <path d="M278 343 C330 290 362 205 353 114 C372 200 348 292 292 343 Z" fill="#f3f3f3"/>
      <path d="M126 343 C252 312 348 232 353 114 C362 205 330 290 278 343 Z" fill="url(#steel-swoosh)"/>
      <circle cx="353" cy="114" r="12" fill="#e8402a"/>
    </svg>

    <div class="brand-lockup">
      <span class="brand-name">Torvane Halbridge</span>
      <span class="brand-dot"></span>
    </div>

    <div class="contact-block">
      <p class="person-name">DALEN MORROW</p>
      <p class="person-role">CEO/FOUNDER</p>
      <p class="address">4120 Larkspur Court<br>Brightwater, Oregon 97215</p>
      <ul class="contact-list">
        <li>503 218 4470
          <svg class="contact-icon" viewBox="0 0 16 16"><path d="M3.5 1 6 1.5 7 5 5.3 6.3C6.2 8.2 7.8 9.8 9.7 10.7L11 9l3.5 1 .5 2.5C15 14 13.8 15 12.5 15 6.7 14.6 1.4 9.3 1 3.5 1 2.2 2 1 3.5 1Z"/></svg>
        </li>
        <li>503 771 2093
          <svg class="contact-icon" viewBox="0 0 16 16"><path d="M4.5 0h7A1.5 1.5 0 0 1 13 1.5v13a1.5 1.5 0 0 1-1.5 1.5h-7A1.5 1.5 0 0 1 3 14.5v-13A1.5 1.5 0 0 1 4.5 0Zm.5 2v10h6V2Zm3 11a1 1 0 1 0 0 2 1 1 0 0 0 0-2Z"/></svg>
        </li>
        <li>503 218 4471
          <svg class="contact-icon" viewBox="0 0 16 16"><path d="M4 1h8v4H4Zm-2 5h12a1 1 0 0 1 1 1v5h-3v3H4v-3H1V7a1 1 0 0 1 1-1Zm3 5v3h6v-3Z"/></svg>
        </li>
        <li>dalen@torvane.example
          <svg class="contact-icon" viewBox="0 0 16 16"><path d="M1 3h14v1.2L8 8.6 1 4.2Zm0 2.6 7 4.4 7-4.4V13H1Z"/></svg>
        </li>
        <li>www.torvane.example
          <svg class="contact-icon" viewBox="0 0 16 16"><path d="M8 1a7 7 0 1 0 0 14A7 7 0 0 0 8 1Zm-4.6 6H6c.1-1.8.5-3.3 1.1-4.3A5.5 5.5 0 0 0 3.4 7Zm0 2a5.5 5.5 0 0 0 3.7 4.3C6.5 12.3 6.1 10.8 6 9Zm4.6-2h2.1C10 5 9.1 2.8 8 2.6 6.9 2.8 6 5 5.9 7Zm0 2H5.9c.1 2 1 4.2 2.1 4.4 1.1-.2 2-2.4 2.1-4.4Zm1.9-2h2.6a5.5 5.5 0 0 0-3.7-4.3c.6 1 1 2.5 1.1 4.3Zm0 2c-.1 1.8-.5 3.3-1.1 4.3A5.5 5.5 0 0 0 12.6 9Z"/></svg>
        </li>
      </ul>
    </div>
  </section>

  <section class="card card-back">
    <div class="back-brand">
      <span class="back-brand-name">Torvane Halbridge</span>
      <span class="back-brand-dot"></span>
    </div>
    <p class="back-url">www.torvanehalbridge.example</p>
  </section>
</body>
</html>
```